Business Card Design for Marketing Firm

Looking for business card design for higher end marketing firm. Clean but impressionable/trendy. We are a marketing firm that represents manufacturers in the foodservice equipment and supply industry. Our customers are end users such has hotels, restaurants, country clubs, convention centers and casinos as well as distributors of restaurants supplies and equipment, and manufacturers of foodservice equipment and supplies.
Target Market(s)
Hotels, Restaurants, Supply & Equipment Distributors, Foodservice Manufacturers
Industry/Entity Type
Foodservice/Hospitality
Contact Information for Business Card
Name, Title, Contact Number, Email, Website, Social Media, Address
Requirements
Must have
- Clean & Simple but Serious and Impressionable

```html
<!DOCTYPE html>
<html lang="en">
<head>
<meta charset="utf-8">
<title>Meridian Hospitality Reps — Business Card</title>
<link rel="stylesheet" href="https://fonts.googleapis.com/css2?family=Montserrat:wght@500;800&display=swap">
<style>
  :root {
    --navy: #2b2a7e;
    --white: #ffffff;
    --ink: #1d1d2b;
    --backdrop: #e9e9ee;
  }
  * { margin: 0; padding: 0; box-sizing: border-box; }
  html, body { width: 1200px; height: 900px; overflow: hidden; }
  body {
    background: var(--backdrop);
    font-family: "Montserrat", Arial, sans-serif;
    position: relative;
  }
  .card {
    position: absolute;
    left: 300px;
    width: 600px;
    height: 343px;
    border-radius: 24px;
    overflow: hidden;
    box-shadow: 0 6px 18px rgba(0,0,0,0.12);
  }
  .card--front { top: 86px; background: var(--navy); }
  .card--back { top: 472px; background: var(--white); }

  .brand {
    position: absolute;
    display: flex;
    flex-direction: column;
    align-items: center;
    gap: 10px;
    font-weight: 800;
    text-transform: uppercase;
    text-align: center;
  }
  .brand__mark {
    width: 46px; height: 46px;
    border-radius: 50%;
    border: 2px solid currentColor;
  }
  .brand__name { font-size: 24px; letter-spacing: 0.06em; line-height: 1.15; }
  .brand__sub { font-size: 14px; letter-spacing: 0.3em; }

  .card--front .brand { color: var(--white); left: 0; right: 0; top: 100px; }
  .card--back .brand { color: var(--navy); left: 30px; width: 280px; top: 100px; }
  .card--back .brand__name { font-size: 20px; }

  .divider {
    position: absolute;
    left: 330px; top: 60px;
    width: 2px; height: 220px;
    background: var(--navy);
  }
  .contact {
    position: absolute;
    left: 352px; top: 58px;
    color: var(--ink);
    font-weight: 500;
    font-size: 12.5px;
    line-height: 1.45;
  }
  .contact__name { color: var(--navy); font-weight: 800; font-size: 19px; line-height: 1.1; }
  .contact__title { margin-bottom: 10px; }
  .contact__address { margin-bottom: 10px; }
  .contact__row { display: flex; align-items: center; gap: 8px; }
  .contact__row svg { width: 14px; height: 14px; flex: none; }
  .social { display: flex; align-items: center; gap: 5px; }
  .social__dot { width: 14px; height: 14px; border-radius: 50%; background: var(--navy); }
  .social__handle { margin-left: 4px; }

  .band {
    position: absolute;
    left: 0; right: 0; bottom: 0;
    height: 28px;
    background: var(--navy);
  }
</style>
</head>
<body>
  <section class="card card--front" aria-label="Card front">
    <div class="brand">
      <span class="brand__mark" aria-hidden="true"></span>
      <span class="brand__name">Meridian Hospitality</span>
      <span class="brand__sub">Reps</span>
    </div>
  </section>

  <section class="card card--back" aria-label="Card back">
    <div class="brand">
      <span class="brand__mark" aria-hidden="true"></span>
      <span class="brand__name">Meridian Hospitality</span>
      <span class="brand__sub">Reps</span>
    </div>

    <div class="divider" aria-hidden="true"></div>

    <div class="contact">
      <p class="contact__name">DANIEL HART</p>
      <p class="contact__title">Co-Founder</p>
      <p class="contact__address">P.O. BOX 45-20 NRT-12<br>Linden St 14, Fairview</p>
      <p class="contact__row">
        <svg viewBox="0 0 16 16" aria-hidden="true"><path fill="#2b2a7e" d="M3 1h3l1.5 4-2 1.3a9 9 0 0 0 4.2 4.2L11 8.5l4 1.5v3a2 2 0 0 1-2 2A12 12 0 0 1 1 3a2 2 0 0 1 2-2z"/></svg>
        555-014-2290
      </p>
      <p class="contact__row">
        <svg viewBox="0 0 16 16" aria-hidden="true"><rect x="1" y="3" width="14" height="10" rx="1" fill="#2b2a7e"/><path d="M1.5 3.5 8 9l6.5-5.5" stroke="#fff" stroke-width="1.3" fill="none"/></svg>
        info@meridianreps.com
      </p>
      <p class="contact__row">
        <svg viewBox="0 0 16 16" aria-hidden="true"><circle cx="8" cy="8" r="6.5" fill="none" stroke="#2b2a7e" stroke-width="1.5"/><ellipse cx="8" cy="8" rx="2.8" ry="6.5" fill="none" stroke="#2b2a7e" stroke-width="1.2"/><path d="M1.5 8h13" stroke="#2b2a7e" stroke-width="1.2"/></svg>
        www.meridianreps.com
      </p>
      <p class="contact__row social">
        <span class="social__dot" aria-hidden="true"></span>
        <span class="social__dot" aria-hidden="true"></span>
        <span class="social__dot" aria-hidden="true"></span>
        <span class="social__dot" aria-hidden="true"></span>
        <span class="social__handle">@meridianreps</span>
      </p>
    </div>

    <div class="band" aria-hidden="true"></div>
  </section>
</body>
</html>
```